Carwash Signage

We own and operate a 25m tunnel car wash in the uk. We are looking to upgrade our signage to include the following:-

Wash selection Board Size-1300x1300mm
Conditions 1300x1300mm
Instructions 1300x1300mm
Banner 2600x600mm
Stamp card flyer a5 double sided - 9 squares for stamping 3rd square needs to say free air freshener 9th square needs to say free vip car wash.

I have attached some notes for the details that are required to be included.

We are looking for a modern smart look more European car wash style than American car wash style. It should be bold and clear. with yellow/orange & blue/green,grey colours

The final design must be in a industry standard printable format.

UPDATED BRIEF AS DISCUSSED: We require design for 2 x window decals, flag design and 50% off voucher. Attached are rough layout drawings of what they should look like - we expect the designs to be in keeping with the previous designs colours, etc that have been carried out. We Look forward to hearing from you.

Target Market(s)

local car owners within a 15-20 mile radius

Colors
0054AA
0677BA
7BADD7
CADEEF
E8F1F8
0094D4
00A9DD
6FCCEA
C7EBF8
E9F6FB
00AB8E
00BBA5
67D7C9
C6EFE9
E9F9F6

Requirements
Must have
• must be sharp and modern European look

```html
<!DOCTYPE html>
<html lang="en">
<head>
<meta charset="utf-8">
<title>Harbourline Car Wash – Wash Selection Board</title>
<link href="https://fonts.googleapis.com/css2?family=Montserrat:wght@700;800&family=Arimo:wght@700&display=swap" rel="stylesheet">
<style>
  :root {
    --backdrop: #8c8c8c;
    --board-top: #1d7099;
    --board-bottom: #1f3c56;
    --title-gold: #f6b419;
    --grid-gold: #d6a630;
    --star-yellow: #f7ea1d;
    --pay-yellow: #f4e31f;
    --text-white: #ffffff;
    --logo-navy: #1b2f7a;
  }
  html, body {
    margin: 0;
    width: 1200px;
    height: 1000px;
    overflow: hidden;
    background: var(--backdrop);
  }
  .board {
    position: absolute;
    left: 197px;
    top: 97px;
    width: 806px;
    height: 806px;
    background: linear-gradient(180deg, var(--board-top) 0%, #1f4f72 45%, var(--board-bottom) 100%);
    box-shadow: 0 4px 14px rgba(0,0,0,0.35);
    font-family: "Arimo", Arial, sans-serif;
    color: var(--text-white);
  }
  .brand {
    position: absolute;
    left: 15px;
    top: 15px;
    width: 196px;
    height: 67px;
    background: #fff;
    display: flex;
    align-items: center;
    justify-content: center;
    gap: 8px;
  }
  .brand-dot {
    width: 18px;
    height: 18px;
    border-radius: 50%;
    background: var(--logo-navy);
  }
  .brand-name {
    font-family: "Montserrat", sans-serif;
    font-weight: 800;
    font-size: 15px;
    line-height: 1.05;
    color: var(--logo-navy);
    text-transform: uppercase;
  }
  .board-title {
    position: absolute;
    left: 0;
    top: 94px;
    width: 100%;
    margin: 0;
    text-align: center;
    font-family: "Montserrat", sans-serif;
    font-weight: 800;
    font-size: 63px;
    line-height: 64px;
    color: var(--title-gold);
    letter-spacing: 1px;
  }
  .wash-table {
    position: absolute;
    left: 6px;
    top: 250px;
    width: 794px;
    border-collapse: collapse;
    table-layout: fixed;
  }
  .wash-table td, .wash-table th {
    border: 2px solid var(--grid-gold);
    padding: 0;
    text-align: center;
    vertical-align: middle;
    font-weight: 700;
  }
  .feature {
    font-size: 9px;
    line-height: 10px;
    text-transform: uppercase;
  }
  .options-head span {
    display: inline-block;
    transform: rotate(-35deg);
    font-size: 12px;
    margin-top: 14px;
  }
  .price-head { font-size: 16px; }
  .tier { font-size: 13px; line-height: 15px; }
  .star {
    color: var(--star-yellow);
    font-size: 30px;
    line-height: 20px;
    padding-top: 10px !important;
  }
  .price { font-size: 12px; }
  .head-row { height: 68px; }
  .offers-row { height: 68px; }
  .offers-cell { position: relative; }
  .offers-cell div { position: absolute; top: 50%; transform: translate(-50%, -50%); white-space: nowrap; }
  .offers-label { left: 123px; font-size: 15px; }
  .offers-pack { left: 310px; font-size: 14px; line-height: 17px; }
  .offers-loyalty { left: 583px; font-size: 14px; line-height: 17px; }
  .offers-loyalty small { font-size: 11px; }
  .payment {
    position: absolute;
    left: 0;
    top: 587px;
    width: 100%;
    text-align: center;
    font-family: "Montserrat", sans-serif;
    font-weight: 800;
    color: var(--pay-yellow);
  }
  .payment-label { font-size: 37px; line-height: 46px; display: block; }
  .payment-methods { font-size: 63px; line-height: 72px; display: block; }
  .rule {
    position: absolute;
    left: 87px;
    top: 748px;
    width: 611px;
    height: 3px;
    background: var(--text-white);
  }
</style>
</head>
<body>
<main class="board">
  <div class="brand">
    <span class="brand-dot"></span>
    <span class="brand-name">Harbourline<br>Car Wash</span>
  </div>

  <h1 class="board-title">WASH SELECTION<br>BOARD</h1>

  <table class="wash-table">
    <colgroup>
      <col style="width:86px"><col style="width:79px"><col style="width:62px"><col style="width:51px">
      <col style="width:67px"><col style="width:79px"><col style="width:65px"><col style="width:54px">
      <col style="width:69px"><col style="width:52px"><col style="width:62px"><col style="width:68px">
    </colgroup>
    <tr class="head-row">
      <th class="options-head"><span>OPTIONS</span></th>
      <th class="feature">Roof brush &amp; contour brushes sill brushes</th>
      <th class="feature">Drying dolible contour</th>
      <th class="feature">Waxing</th>
      <th class="feature">Hand brush prepared</th>
      <th class="feature">Active foam pre soak</th>
      <th class="feature">Alloy wheel spray</th>
      <th class="feature">Jade ultra wax</th>
      <th class="feature">Jet wash pre wash</th>
      <th class="feature">Under body wash</th>
      <th class="feature">Snow wash pre wash</th>
      <th class="price-head">PRICE</th>
    </tr>
    <tr style="height:47px">
      <td class="tier">VIP<br>PLATINUM</td>
      <td class="star">*</td><td class="star">*</td><td class="star">*</td><td class="star">*</td><td class="star">*</td>
      <td class="star">*</td><td class="star">*</td><td class="star">*</td><td class="star">*</td><td class="star">*</td>
      <td class="price">£10.00</td>
    </tr>
    <tr style="height:36px">
      <td class="tier">GOLD</td>
      <td class="star">*</td><td class="star">*</td><td class="star">*</td><td class="star">*</td><td class="star">*</td>
      <td class="star">*</td><td class="star">*</td><td class="star">*</td><td></td><td></td>
      <td class="price">£8.50</td>
    </tr>
    <tr style="height:36px">
      <td class="tier">SILVER</td>
      <td class="star">*</td><td class="star">*</td><td class="star">*</td><td class="star">*</td><td class="star">*</td>
      <td></td><td></td><td></td><td></td><td></td>
      <td class="price">£7.50</td>
    </tr>
    <tr style="height:35px">
      <td class="tier">BRONZE</td>
      <td class="star">*</td><td class="star">*</td><td class="star">*</td><td class="star">*</td>
      <td></td><td></td><td></td><td></td><td></td><td></td>
      <td class="price">£6.50</td>
    </tr>
    <tr class="offers-row">
      <td class="offers-cell" colspan="12">
        <div class="offers-label">OFFERS</div>
        <div class="offers-pack">VIP PLATINUM WASH PACK<br>BUY 2 GET 1 FREE&nbsp; E20.00</div>
        <div class="offers-loyalty">LOYALTY CARD AVAILABLE<br>WASH + EARN<br><small>ASK THE OPERATOR FOR DETAILS</small></div>
      </td>
    </tr>
  </table>

  <p class="payment">
    <span class="payment-label">PAYMENT ACCEPTED</span>
    <span class="payment-methods">CASH / CARD</span>
  </p>

  <div class="rule"></div>
</main>
</body>
</html>
```